Family business needs stationery redesign with new logo

Family owned company, established in 1987 wanting a brand 'refresh'. We are an electrical, refrigeration and construction company based in the Barkly Region Northern Territory, Australia. We have a new logo we would like to use which is uploaded along with our current letterhead and email signature. We are also dropping the word 'contractors' so please do not include this on any designs. Please note also, the 'orange' color used in our logo and designs should be Northern Territory red ochre which is as follows:

RGB (Hex): #C75B12
PantoneĀ® 159 C
CMYK: 1 / 74 / 100 / 7

We are needing our stationery redesigned using our new logo. Please include letterheads, business cards, envelopes, and email signatures.

We currently use our business letterheads for quotations, invoices, letters, HR matters, and internal memos.

We also need a separate simplified letterhead for internal paperwork such as employee leave forms, meeting agendas, and meeting minutes etc.

Reason: Needing more submissions of full package designs. We are wanting all our stationery, including business cards, letterheads, email signatures, envelopes, etc to be cohesive. We also require ALL the information, as supplied on our template letterhead, to be included on the new letterhead designs. including electrical license no.etc Thank you, R&W

Reason: needing more time as work has got in the way of looking over designs. A lot of designs not meeting the brief/criteria.

Industry/Entity Type

Business

Colors
0355a3
f37122

Requirements
Must have
• The 'orange' color used in the designs should be Northern Territory red ochre which is as follows:
• RGB (Hex): #C75B12
• PantoneĀ® 159 C
• CMYK: 1 / 74 / 100 / 7
• ***MUST INCLUDE ALL INFORMATION THAT IS ON OUR CURRENT LETTERHEAD***
Should not have
• Please do not include the word 'contractors'

```html
<!DOCTYPE html>
<html lang="en">
<head>
<meta charset="utf-8">
<title>R&amp;W Stationery</title>
<link href="https://fonts.googleapis.com/css2?family=Source+Sans+3:wght@400;600;700;800&display=swap" rel="stylesheet">
<style>
  :root{
    --navy:#1f2f6c;
    --ochre:#c75b12;
    --paper:#ffffff;
    --ink:#333333;
    --bg:#e3e3e3;
  }
  *{box-sizing:border-box;margin:0;padding:0}
  html,body{width:1200px;height:715px;overflow:hidden}
  body{background:var(--bg);font-family:"Source Sans 3",Arial,sans-serif;color:var(--ink);position:relative}
  .sheet{position:absolute;background:var(--paper)}
  .tab{position:absolute;width:6px}
  .tab--navy{background:var(--navy)}
  .tab--ochre{background:var(--ochre)}
  .wordmark{position:absolute;font-weight:800;color:var(--navy);line-height:1;letter-spacing:1px;text-align:center}

  /* Letterhead */
  .letterhead{left:188px;top:66px;width:440px;height:620px;z-index:1}
  .letterhead .tab--navy{left:0;top:40px;height:54px}
  .letterhead .tab--ochre{right:0;top:40px;height:64px;border-radius:4px 0 0 4px}
  .letterhead .wordmark{left:0;right:0;top:44px;font-size:44px}
  .tagline{position:absolute;left:0;right:0;top:98px;text-align:center;font-size:10px;color:var(--navy)}
  .body-copy{position:absolute;left:33px;top:224px;width:384px;font-size:7.6px;line-height:9.6px;color:#222}
  .body-copy p{margin-bottom:9.6px}
  .signoff{position:absolute;left:33px;top:405px;font-size:8px;color:#222}
  .lh-footer{position:absolute;left:0;right:0;top:570px;text-align:center;font-size:8px;line-height:11px;color:#444}
  .lh-footer b{color:var(--ochre);font-weight:700}

  /* Business cards */
  .card{position:absolute;overflow:hidden;z-index:2}
  .card--front{left:48px;top:160px;width:240px;height:136px;background:var(--paper);border-radius:8px}
  .card--front .tab--navy{left:0;top:90px;height:34px;width:4px}
  .card--front .tab--ochre{right:0;top:90px;height:34px;width:5px}
  .card--front .wordmark{left:0;right:0;top:22px;font-size:34px}
  .card--wide{left:748px;top:44px;width:284px;height:138px;background:var(--paper)}
  .card--wide .tab--navy{left:0;top:86px;height:44px;width:6px}
  .card--wide .tab--ochre{right:0;top:86px;height:44px;width:6px}
  .card--wide .wordmark{left:0;right:0;top:20px;font-size:38px}
  .person{position:absolute;font-size:6.4px;line-height:8.6px;color:#444}
  .person .name{font-size:9px;font-weight:600;color:var(--navy);line-height:10px}
  .person .role{color:var(--ochre)}
  .card--wide .person{left:20px;top:91px;font-size:7.2px;line-height:10px}
  .card--wide .person .name{font-size:11px;line-height:12px}
  .card--front .person{left:15px;top:89px}
  .contacts{position:absolute;text-align:right;font-size:6.4px;line-height:9.2px;color:#444}
  .contacts span{display:flex;justify-content:flex-end;align-items:center;gap:3px}
  .contacts svg{width:6px;height:6px;fill:var(--navy)}
  .card--front .contacts{right:14px;top:92px}
  .card--wide .contacts{right:16px;top:90px;font-size:7.2px;line-height:10.6px}
  .card--wide .contacts svg{width:7px;height:7px}
  .card--back{left:48px;width:240px;height:137px;background:var(--ochre);border-radius:8px}
  .card--back .wordmark{left:0;right:0;top:42px;font-size:44px;color:#fff}
  .est{position:absolute;left:0;right:0;top:112px;text-align:center;font-size:9.5px;letter-spacing:.5px}
  .card--back-a{top:324px}
  .card--back-a .est{color:#fff}
  .card--back-b{top:482px}
  .card--back-b .est{color:var(--navy)}

  /* Envelopes */
  .envelope-back{left:642px;top:210px;width:518px;height:232px}
  .envelope-back svg{position:absolute;left:0;top:0}
  .envelope-back .wordmark{left:0;right:0;top:28px;font-size:32px;color:#fff}
  .envelope-front{left:642px;top:457px;width:518px;height:231px}
  .envelope-front .tab--navy{left:0;top:15px;height:64px}
  .envelope-front .tab--ochre{right:0;top:15px;height:64px;border-radius:4px 0 0 4px}
  .envelope-front .wordmark{left:24px;top:30px;font-size:40px}
  .return-address{position:absolute;left:25px;top:188px;font-size:8px;line-height:11px;color:#444}
</style>
</head>
<body>

<section class="sheet letterhead">
  <div class="tab tab--navy"></div>
  <div class="tab tab--ochre"></div>
  <div class="wordmark">R&amp;W</div>
  <div class="tagline">Electrical - Refrigeration - Building Services</div>
  <div class="body-copy">
    <p>Lorem ipsum dolor sit amet, consectetur adipiscing elit. Donec orci purus, luctus vitae dignissim eu, iaculis sed purus. Vivamus faucibus, ipsum nec aliquet viverra, leo mauris condimentum ligula, sit amet sagittis enim ligula quis arcu. Nam egestas tortor id nisi porttitor mattis. In tortor ante, ultricies in suscipit a, tempus non massa. Vivamus et auctor mi.</p>
    <p>Nulla facilisi. Aliquam erat volutpat. Phasellus nec eros mauris, et scelerisque orci. Donec malesuada orci vitae nulla accumsan scelerisque accumsan iaculis magna sit amet fringilla. Maecenas consequat, magna eget tincidunt rutrum mi, id feugiat ante nisi eu risus. Vestibulum nunc orci, rhoncus a placerat in, ultricies varius eros, vel fringilla nisi suscipit eget.</p>
    <p>Curabitur sagittis nulla at porttitor. Mauris a justo et tellus interdum tristique. Sed id augue vitae urna aliquet a quam. Pellentesque arcu velit, cursus et malesuada ut, consequat et diam. Nullam ullamcorper vitae, rhoncus et dolor. In ultricies ultricies nulla, ut rutrum nisi iaculis at. Donec ornare faucibus.</p>
    <p>Aenean varius ultricies. Morbi semper, est id tincidunt gravida, sem arcu adipiscing lacus, ac bibendum lorem. Quisque nec diam sed risus consectetur a accumsan quis quis nibh. Vestibulum id purus lorem.</p>
  </div>
  <div class="signoff">Sam Porter</div>
  <div class="lh-footer">
    24 Ridge St, PO Box, Banka Flat NT. 0860<br>
    ABN 12 345 678 | Refrigerant Trading Authorisation 100234 | NT Electrical Contractors License 40321<br>
    <b>P :</b> 08 8900 1234 &nbsp;<b>F :</b> 08 8900 5678 &nbsp;<b>E :</b> info@rwservices.com.au &nbsp;<b>W :</b> rwservices.com.au
  </div>
</section>

<section class="card card--front">
  <div class="tab tab--navy"></div>
  <div class="tab tab--ochre"></div>
  <div class="wordmark">R&amp;W</div>
  <div class="person">
    <div class="name">ALEX CARTER</div>
    <div class="role">CEO/FOUNDER</div>
    <div>412 Wattle Road</div>
    <div>Darwin NT 0800</div>
  </div>
  <div class="contacts">
    <span>555 210 4417 <svg viewBox="0 0 10 10"><path d="M2 0l2 2-1 1.5c.6 1.4 1.8 2.6 3.3 3.3L7.8 5.8 10 8 8.5 9.8C4 9.5.5 6 0 1.5z"/></svg></span>
    <span>555 210 4418 <svg viewBox="0 0 10 10"><path d="M2.5 0h5v3h-5zM0 3.5h10V8H8v2H2V8H0zM3 6.5v2.5h4V6.5z"/></svg></span>
    <span>alex@rwservices.com.au <svg viewBox="0 0 10 10"><path d="M0 1.5h10v7H0zM1 2.5l4 3 4-3"/></svg></span>
    <span>www.rwservices.com.au <svg viewBox="0 0 10 10"><circle cx="5" cy="5" r="5"/></svg></span>
  </div>
</section>

<section class="card card--back card--back-a">
  <div class="wordmark">R&amp;W</div>
  <div class="est">Est. 1987</div>
</section>

<section class="card card--back card--back-b">
  <div class="wordmark">R&amp;W</div>
  <div class="est">Est. 1987</div>
</section>

<section class="card card--wide">
  <div class="tab tab--navy"></div>
  <div class="tab tab--ochre"></div>
  <div class="wordmark">R&amp;W</div>
  <div class="person">
    <div class="name">ALEX CARTER</div>
    <div class="role">CEO/FOUNDER</div>
    <div>412 Wattle Road</div>
    <div>Darwin NT 0800</div>
  </div>
  <div class="contacts">
    <span>555 210 4417 <svg viewBox="0 0 10 10"><path d="M2 0l2 2-1 1.5c.6 1.4 1.8 2.6 3.3 3.3L7.8 5.8 10 8 8.5 9.8C4 9.5.5 6 0 1.5z"/></svg></span>
    <span>555 210 4418 <svg viewBox="0 0 10 10"><path d="M2.5 0h5v3h-5zM0 3.5h10V8H8v2H2V8H0zM3 6.5v2.5h4V6.5z"/></svg></span>
    <span>alex@rwservices.com.au <svg viewBox="0 0 10 10"><path d="M0 1.5h10v7H0zM1 2.5l4 3 4-3"/></svg></span>
    <span>www.rwservices.com.au <svg viewBox="0 0 10 10"><circle cx="5" cy="5" r="5"/></svg></span>
  </div>
</section>

<section class="sheet envelope-back">
  <svg width="518" height="232" viewBox="0 0 518 232">
    <rect width="518" height="232" fill="#ffffff"/>
    <path d="M0 232 L195 130 M518 232 L323 130" stroke="#d6d6d6" stroke-width="1.2" fill="none"/>
    <path d="M0 0 H518 L510 60 Q505 84 480 84 H38 Q13 84 8 60 Z" fill="var(--ochre)"/>
  </svg>
  <div class="wordmark">R&amp;W</div>
</section>

<section class="sheet envelope-front">
  <div class="tab tab--navy"></div>
  <div class="tab tab--ochre"></div>
  <div class="wordmark">R&amp;W</div>
  <div class="return-address">24 Ridge St, PO Box<br>Banka Flat NT. 0860</div>
</section>

</body>
</html>
```